Tallowmere Cornerstones

Need to improve polish and professionalism of PPT presentation. Get consistent look and feel through whole slides, improved look and feel while maintaining the corporate standards/colour scheme, from the Brackwyn corporate presentation. Need everything in Arial font with colours consistent with the PPT template

```html
<!DOCTYPE html>
<html lang="en">
<head>
<meta charset="utf-8">
<title>Tallowmere Cornerstones – Slide Overview</title>
<link rel="stylesheet" href="https://fonts.googleapis.com/css2?family=Arimo:wght@400;700&display=swap">
<style>
  :root{
    --canvas:#a6a6a6;
    --paper:#ffffff;
    --ink:#1b1b1b;
    --ink-soft:#3a3a3a;
    --red:#c0161f;
    --red-soft:#cf3a45;
    --night:#172222;
    --night-2:#1c2729;
    --blue:#1262c2;
    --purple:#7a1f6c;
    --green:#2f7d1f;
    --yellow:#f4ee00;
    --down:#b3121f;
    --grey-panel:#e3e3e3;
    --muted:#8d9597;
  }
  *{box-sizing:border-box;margin:0;padding:0}
  html,body{width:1012px;height:1200px;overflow:hidden;background:var(--canvas)}
  body{position:relative;font-family:"Arimo",Arial,sans-serif;color:var(--ink)}
  .slide{position:absolute;width:459px;height:258px;background:var(--paper);overflow:hidden}
  .col-l{left:32px}.col-r{left:521px}
  .row-1{top:38px}.row-2{top:326px}.row-3{top:615px}.row-4{top:904px}
  .abs{position:absolute}
  .title{position:absolute;font-weight:700;font-size:10.5px;line-height:14px;letter-spacing:.1px;color:var(--ink)}
  .footer{position:absolute;left:0;bottom:0;width:100%;height:19px;background:var(--night);color:#fff}
  .brand{position:absolute;left:35px;top:4px;display:flex;align-items:flex-end;gap:2px}
  .brand-name{font-weight:700;font-size:10.5px;line-height:11px;letter-spacing:.4px;color:#fff}
  .brand-sub{font-size:3.6px;line-height:3.8px;color:var(--muted)}
  .copyright{position:absolute;right:34px;top:6.5px;font-size:4.6px;font-weight:700}
  .page-no{position:absolute;right:10px;top:2.5px;width:14px;height:14px;background:var(--red);font-size:4.4px;font-weight:700;display:flex;align-items:center;justify-content:center}
  .tick{position:absolute;width:5px;height:5px;border-radius:50%;background:var(--red)}
  .tick::after{content:"";position:absolute;left:1.5px;top:1px;width:1.2px;height:2.2px;border:solid #fff;border-width:0 .7px .7px 0;transform:rotate(45deg)}
  .body-text{position:absolute;font-size:5.7px;line-height:9.4px;color:var(--ink-soft)}
  .lead{position:absolute;font-size:6.4px;line-height:9.4px;font-weight:700;color:var(--ink)}
  .photo{position:absolute}
  .bullet{color:var(--red)}

  /* slide 1 */
  .cover-bg{position:absolute;inset:0;background:linear-gradient(180deg,#25362f 0%,#2a3b3a 40%,#4e3e5a 48%,#5d4a68 60%,#3b2c40 80%,#2b2130 100%)}
  .cover-brand{position:absolute;left:0;width:100%;top:24px;display:flex;justify-content:center;align-items:flex-end;gap:3px}
  .cover-brand .brand-name{font-size:23px;line-height:24px;letter-spacing:1px}
  .cover-brand .brand-sub{font-size:8px;line-height:9px;color:#8a9693}
  .cover-title{position:absolute;left:0;width:100%;top:62px;text-align:center;color:#fff;font-weight:700;font-size:14px;line-height:17px}

  /* figure placeholders */
  .chart-area{position:absolute;background:linear-gradient(180deg,#f1f1f1 0%,#bdbdbd 100%);border-radius:2px}
  .cycle-area{position:absolute;border-radius:50%;background:radial-gradient(circle,#ffffff 0%,#f3f3f3 55%,#dedede 100%)}

  /* slide 2 */
  .fund-list{position:absolute;left:222px;top:61px;width:215px;font-size:5.6px;color:var(--ink-soft)}
  .fund-list p{position:absolute;white-space:nowrap}

  /* slide 3 */
  .node{position:absolute;display:flex;align-items:center;justify-content:center;text-align:center;font-size:4.6px;font-weight:700;line-height:6px}
  .node-prod{left:65px;top:101px;width:58px;height:43px;background:var(--night);color:#fff;border-radius:2px;flex-direction:column;gap:4px;font-size:5.6px}
  .node-sub{top:163px;width:61px;height:20px;border:.7px solid #777;border-radius:2px;background:#fff;color:var(--ink)}
  .venn-label{position:absolute;color:#fff;font-size:4.4px;font-weight:700;text-align:center;width:50px;line-height:6px}

  /* slide 4 */
  .tu{position:absolute;display:flex;align-items:center;justify-content:center;font-size:5.3px;font-weight:700;color:#fff;border:.5px solid #0d1d3a}

  /* slide 8 */
  .thanks{position:absolute;inset:0;background:radial-gradient(ellipse at 50% 55%,#202c2e 0%,var(--night-2) 60%,#141c1e 100%)}
</style>
</head>
<body>

<!-- Slide 01: cover -->
<section class="slide col-l row-1">
  <div class="cover-bg" role="img" aria-label="Haul trucks driving along a mine road at dusk with the pit in the background"></div>
  <div class="cover-brand"><span class="brand-name">BRACKWYN</span><span class="brand-sub">Mining<br>Solutions</span></div>
  <h1 class="cover-title">TALLOWMERE CORNERSTONES<br>KPIS &amp; PRODUCTION FUNDAMENTALS</h1>
</section>

<!-- Slide 05: payload distribution -->
<section class="slide col-r row-1">
  <svg class="abs" style="left:0;top:0" width="459" height="258" viewBox="0 0 459 258" aria-hidden="true">
    <path d="M365 0H459V240H365V220H424.5V27.5H365Z" fill="var(--red)"/>
  </svg>
  <h2 class="title" style="left:34px;top:12px">EQUIPMENT PRODUCTIVITY<br>– HAUL TRUCKS</h2>
  <div class="chart-area" style="left:34px;top:74px;width:226px;height:114px" role="img" aria-label="Payload distribution chart: number of loads against percent of target payload from 80 to 120, with productivity, durability and tested limit zones, 50 percent below target and 10 percent between 110 and 120"></div>
  <span class="tick" style="left:284px;top:87px"></span>
  <p class="body-text" style="left:294px;top:83px;width:110px">To increase productivity, we want to maximize truck payload while adhering to the 10/10/20 rule</p>
  <span class="tick" style="left:284px;top:126px"></span>
  <p class="body-text" style="left:294px;top:122px;width:110px">No more than 10% of loads between 110% and 120% of Nominal Payload</p>
  <span class="tick" style="left:284px;top:154.5px"></span>
  <p class="body-text" style="left:294px;top:150.5px;width:110px">No loads greater than 120% of Nominal Payload</p>
  <footer class="footer"><div class="brand"><span class="brand-name">BRACKWYN</span><span class="brand-sub">Mining<br>Solutions</span></div><span class="copyright">© Copyrights 2024 | All Rights Reserved</span><span class="page-no">05</span></footer>
</section>

<!-- Slide 02: module goals -->
<section class="slide col-l row-2">
  <div class="abs" style="left:0;top:0;width:92px;height:240px;background:var(--red)"></div>
  <div class="photo" style="left:35px;top:37px;width:174.5px;height:188px;background:linear-gradient(180deg,#5a87c8 0%,#9bb3d2 25%,#b6a38b 45%,#d76a2f 60%,#9f8b72 80%,#6f6254 100%)" role="img" aria-label="Two mine workers in hard hats on a pit lookout, one in hi-vis orange pointing across the pit"></div>
  <h2 class="title" style="left:132px;top:12px">KPI &amp; PRODUCTION FUNDAMENTALS</h2>
  <div class="fund-list">
    <p class="lead" style="left:0;top:0">At the end of this module, you will understand</p>
    <p style="left:0;top:15px">1.&nbsp;&nbsp;&nbsp;Understand the key concepts of mine production KPIs</p>
    <p style="left:10px;top:24.5px"><span class="bullet">✦</span>&nbsp;&nbsp;Time Usage Model</p>
    <p style="left:10px;top:34px"><span class="bullet">✦</span>&nbsp;&nbsp;Availability, Utilization and Productivity</p>
    <p style="left:10px;top:43.5px"><span class="bullet">✦</span>&nbsp;&nbsp;Elements of the haul cycle</p>
    <p style="left:10px;top:53px"><span class="bullet">✦</span>&nbsp;&nbsp;Elements of the loading cycle</p>
    <p style="left:10px;top:62.5px"><span class="bullet">✦</span>&nbsp;&nbsp;How changes in each of these elements impact mine production</p>
    <p style="left:0;top:81px;line-height:9.4px">2.&nbsp;&nbsp;&nbsp;The goal will be to create a baseline of understanding and a common<br>&nbsp;&nbsp;&nbsp;&nbsp;&nbsp;&nbsp;language across the entire mine-ops team</p>
    <p style="left:0;top:110px">3.&nbsp;&nbsp;&nbsp;You may already understand these concepts</p>
    <p style="left:0;top:129px">4.&nbsp;&nbsp;&nbsp;This is the time to ask questions and get clarification!</p>
  </div>
  <footer class="footer"><div class="brand"><span class="brand-name">BRACKWYN</span><span class="brand-sub">Mining<br>Solutions</span></div><span class="copyright">© Copyrights 2024 | All Rights Reserved</span><span class="page-no">02</span></footer>
</section>

<!-- Slide 06: haul cycle -->
<section class="slide col-r row-2">
  <h2 class="title" style="left:34px;top:12px">EQUIPMENT PRODUCTIVITY – HAUL TRUCKS</h2>
  <p class="lead" style="left:34px;top:52px;width:160px;font-size:5.7px;line-height:9.4px">To minimize cycle time we reduce the time it takes for each haul cycle element</p>
  <span class="tick" style="left:34px;top:81.5px"></span>
  <p class="body-text" style="left:46px;top:77.5px;width:140px">The first step is to try to reduce non-effective time in a haul cycle</p>
  <span class="tick" style="left:34px;top:110.5px"></span>
  <p class="body-text" style="left:46px;top:106.5px;width:140px">What are the non-effective elements of the haul cycle?</p>
  <span class="tick" style="left:34px;top:139.5px"></span>
  <p class="body-text" style="left:46px;top:135.5px;width:140px">What are some ways to reduce non-effective time in a haul cycle?</p>
  <span class="tick" style="left:34px;top:168px"></span>
  <p class="body-text" style="left:46px;top:164px;width:140px">What are the effective elements of a haul cycle?</p>
  <span class="tick" style="left:34px;top:187px"></span>
  <p class="body-text" style="left:46px;top:183px;width:140px">What are some way to reduce effective time in a haul cycle?</p>
  <div class="cycle-area" style="left:229px;top:40px;width:186px;height:186px" role="img" aria-label="Haul cycle diagram of trucks in a loop: stopped empty, traveling empty, wait at shovel, spotting, loading, traveling full, stopped full, wait at dump, dumping"></div>
  <footer class="footer"><div class="brand"><span class="brand-name">BRACKWYN</span><span class="brand-sub">Mining<br>Solutions</span></div><span class="copyright">© Copyrights 2024 | All Rights Reserved</span><span class="page-no">06</span></footer>
</section>

<!-- Slide 03: what makes up production -->
<section class="slide col-l row-3">
  <h2 class="title" style="left:0;width:100%;text-align:center;top:12px">WHAT MAKES UP PRODUCTION</h2>
  <p class="lead" style="left:30px;top:44px">In its simplest terms, we calculate<br>production like this:</p>
  <p class="lead" style="left:186.5px;top:44px">This is true for any process</p>
  <p class="body-text" style="left:186.5px;top:57.5px"><span class="bullet">✦</span>&nbsp;&nbsp;Mowing the lawn<br><span class="bullet">✦</span>&nbsp;&nbsp;Driving<br><span class="bullet">✦</span>&nbsp;&nbsp;Mine Production</p>
  <p class="lead" style="left:319px;top:44px">Production goes up or down<br>because of a change in<br>Equipment Productivity or<br>Operating Time</p>
  <svg class="abs" style="left:0;top:0" width="459" height="240" viewBox="0 0 459 240" aria-hidden="true">
    <path d="M94.3 144V153.5H60.3V163M94.3 153.5H128.3V163" fill="none" stroke="#777" stroke-width=".6"/>
    <circle cx="94.3" cy="144" r="1.1" fill="var(--red)"/>
    <circle cx="60.3" cy="163" r="1.1" fill="var(--red)"/>
    <circle cx="128.3" cy="163" r="1.1" fill="var(--red)"/>
    <g fill="var(--red-soft)" fill-opacity=".88">
      <circle cx="238.7" cy="125.6" r="31"/>
      <circle cx="212.8" cy="173.3" r="31"/>
      <circle cx="262.8" cy="173.3" r="31"/>
    </g>
    <g fill="none" stroke="#fff" stroke-width=".6">
      <rect x="232" y="109" width="13" height="8" rx="1"/>
      <circle cx="212.8" cy="160" r="5"/>
      <rect x="255" y="156" width="14" height="7" rx="1"/>
    </g>
  </svg>
  <div class="node node-prod">
    <svg width="12" height="12" viewBox="0 0 12 12" aria-hidden="true"><circle cx="6" cy="5" r="3" fill="none" stroke="#fff" stroke-width=".8"/><circle cx="6" cy="5" r="1" fill="#fff"/><path d="M2 10.5H10" stroke="#fff" stroke-width=".8"/></svg>
    <span>Production</span>
  </div>
  <div class="node node-sub" style="left:30px">Equipment<br>Productivity</div>
  <div class="node node-sub" style="left:97px">Operating Time</div>
  <span class="venn-label" style="left:213.7px;top:130px">Mowing the lawn</span>
  <span class="venn-label" style="left:187.8px;top:178px">Driving</span>
  <span class="venn-label" style="left:237.8px;top:178px">Mine<br>Production</span>
  <div class="photo" style="left:319px;top:96.4px;width:105.5px;height:106px;border-radius:2px;background:linear-gradient(180deg,#4e5458 0%,#8a9095 35%,#c9c9c6 60%,#d9c79c 75%,#8e9196 100%)" role="img" aria-label="Mine operations control room with rows of desks and monitors"></div>
  <footer class="footer"><div class="brand"><span class="brand-name">BRACKWYN</span><span class="brand-sub">Mining<br>Solutions</span></div><span class="copyright">© Copyrights 2024 | All Rights Reserved</span><span class="page-no">03</span></footer>
</section>

<!-- Slide 07: theory of constraints -->
<section class="slide col-r row-3">
  <h2 class="title" style="left:34px;top:12px">TALLOWMERE CORNERSTONES<br>THE THEORY OF CONSTRAINTS</h2>
  <span class="abs" style="left:0;width:100%;top:113px;text-align:center;font-weight:700;font-size:26px;letter-spacing:1.5px;color:#e4e4e4">BRACKWYN</span>
  <footer class="footer"><div class="brand"><span class="brand-name">BRACKWYN</span><span class="brand-sub">Mining<br>Solutions</span></div><span class="copyright">© Copyrights 2024 | All Rights Reserved</span><span class="page-no">07</span></footer>
</section>

<!-- Slide 04: time usage model -->
<section class="slide col-l row-4">
  <h2 class="title" style="left:0;width:100%;text-align:center;top:12px">GENERIC TIME USAGE MODEL</h2>
  <div class="tu" style="left:39px;top:38.4px;width:381px;height:15.6px;background:var(--blue)">Calendar Time</div>
  <div class="tu" style="left:39px;top:54px;width:254px;height:15.4px;background:var(--blue)">Available Time</div>
  <div class="tu" style="left:293px;top:54px;width:127px;height:6.8px;background:var(--down);font-size:4.8px">Down</div>
  <div class="tu" style="left:39px;top:69.4px;width:126.8px;height:14.9px;background:var(--blue)">Operating Time</div>
  <div class="tu" style="left:39px;top:84.3px;width:63px;height:14.4px;background:var(--blue)">Effective Time</div>
  <div class="tu" style="left:102px;top:84.3px;width:63.8px;height:14.4px;background:var(--purple)">Non-Effective Time</div>
  <div class="tu" style="left:165.8px;top:69.4px;width:63.7px;height:29.3px;background:var(--green)">Operating Delay</div>
  <div class="tu" style="left:229.5px;top:69.4px;width:63.5px;height:29.3px;background:var(--yellow);color:#111">Standby Time</div>
  <div class="tu" style="left:293px;top:60.8px;width:64px;height:37.9px;background:var(--down)">Unscheduled</div>
  <div class="tu" style="left:357px;top:60.8px;width:63px;height:37.9px;background:var(--down)">Scheduled</div>
  <div class="abs" style="left:221px;top:130px;width:200px;height:73px;background:var(--grey-panel)"></div>
  <div class="photo" style="left:40px;top:113px;width:181px;height:109px;background:linear-gradient(180deg,#6c6258 0%,#a6a9ae 30%,#c0b4a6 55%,#b8927a 80%,#8f7868 100%)" role="img" aria-label="Operations room with wall-mounted dashboards and staff standing in discussion"></div>
  <span class="tick" style="left:234px;top:142px"></span>
  <p class="body-text" style="left:246px;top:138px;width:165px">This is a generic Mining time usage model</p>
  <span class="tick" style="left:234px;top:161px"></span>
  <p class="body-text" style="left:246px;top:157px;width:165px;text-align:justify">There may be variations from mine-to-mine (ie Utilized time vs Operating Time) but this model describes everything mine operations needs to know about the time usage of a piece of equipment</p>
  <footer class="footer"><div class="brand"><span class="brand-name">BRACKWYN</span><span class="brand-sub">Mining<br>Solutions</span></div><span class="copyright">© Copyrights 2024 | All Rights Reserved</span><span class="page-no">04</span></footer>
</section>

<!-- Slide 08: closing -->
<section class="slide col-r row-4">
  <div class="thanks"></div>
  <div class="abs" style="left:0;width:100%;top:84px;display:flex;justify-content:center;align-items:flex-end;gap:3px">
    <span class="brand-name" style="font-size:17px;line-height:18px;letter-spacing:.8px">BRACKWYN</span><span class="brand-sub" style="font-size:6.5px;line-height:7px">Mining<br>Solutions</span>
  </div>
  <p class="abs" style="left:0;width:100%;top:108px;text-align:center;color:#fff;font-weight:700;font-size:49px;line-height:54px;letter-spacing:1px">THANK YOU</p>
  <div class="abs" style="left:167.5px;top:165.7px;width:124.5px;height:1.6px;background:var(--red)"></div>
</section>

</body>
</html>
```